gtw school poster design and change logo name

We already have a logo which only needs to be slightly modified with "school".
We also have two advertising faces, a girl and a boy, which should be on our poster.
Important key data:

bilingual D/E small classes
daycare
private kindergarten
private school from 2024

Poster size: 268,5 x 128 cm
We need logo sizes in different sizes
also for T-shirts.
Attached also a old poster

new clients

0094D4
00A9DD
6FCCEA
C7EBF8
E9F6FB
59FF00
82FF00
B8FF75
E3FFCB
F4FFEA
FFC000
F8CF3A
FAE287
FDF2CF
FEFAEE
F0912C
F2A743
F7CA91
FBE8D2
FDF5EE

```html
<!DOCTYPE html>
<html lang="en">
<head>
<meta charset="utf-8">
<title>gtw school – Poster</title>
<link rel="stylesheet" href="https://fonts.googleapis.com/css2?family=Fredoka:wght@600&family=Sniglet:wght@400;800&display=swap">
<style>
  :root {
    --page: #f3f3f1;
    --cream: #e6e3d7;
    --blue: #3f78b0;
    --gold: #d9a12a;
    --white: #ffffff;
  }
  * { margin: 0; padding: 0; box-sizing: border-box; }
  html, body {
    width: 1200px;
    height: 800px;
    overflow: hidden;
    background: var(--page);
  }
  .poster {
    position: absolute;
    left: 20px;
    top: 189px;
    width: 1160px;
    height: 422px;
    background: var(--cream);
    overflow: hidden;
    font-family: "Sniglet", "Fredoka", sans-serif;
  }
  .poster-art {
    position: absolute;
    inset: 0;
    width: 1160px;
    height: 422px;
  }
  .brand {
    position: absolute;
    left: 40px;
    top: 62px;
    width: 240px;
    display: flex;
    align-items: center;
    gap: 10px;
    white-space: nowrap;
  }
  .brand-dot {
    width: 22px;
    height: 22px;
    flex: none;
    border-radius: 50%;
    background: var(--gold);
  }
  .brand-name {
    font-family: "Sniglet", sans-serif;
    font-weight: 800;
    font-size: 30px;
    color: var(--gold);
    line-height: 1;
  }
  .headline {
    position: absolute;
    left: 306px;
    top: 52px;
    font-weight: 800;
    font-size: 50px;
    line-height: 1;
    color: var(--gold);
    white-space: nowrap;
    word-spacing: 4px;
  }
  .headline .accent { color: var(--blue); }
  .offer-title {
    position: absolute;
    left: 28px;
    top: 170px;
    font-family: "Fredoka", sans-serif;
    font-weight: 600;
    font-size: 72px;
    line-height: 1;
    color: var(--gold);
    letter-spacing: 1px;
  }
  .offer-line {
    position: absolute;
    left: 30px;
    font-weight: 800;
    font-size: 33px;
    line-height: 1;
    white-space: nowrap;
  }
  .offer-line.kindergarten { top: 245px; color: var(--white); }
  .offer-line.school { top: 293px; color: var(--gold); }
  .contact-list {
    position: absolute;
    left: 35px;
    top: 342px;
    list-style: none;
  }
  .contact-list li {
    display: flex;
    align-items: center;
    gap: 12px;
    height: 25px;
    font-size: 16px;
    color: var(--white);
    white-space: nowrap;
  }
  .contact-icon {
    width: 18px;
    height: 18px;
    flex: none;
  }
</style>
</head>
<body>
  <main class="poster">
    <svg class="poster-art" viewBox="0 0 1160 422" xmlns="http://www.w3.org/2000/svg">
      <defs>
        <linearGradient id="girl-tones" x1="0" y1="0" x2="0" y2="1">
          <stop offset="0" stop-color="#dfe4ea"/>
          <stop offset="0.6" stop-color="#e8d6c8"/>
          <stop offset="1" stop-color="#f1ece8"/>
        </linearGradient>
        <linearGradient id="boy-tones" x1="0" y1="0" x2="0" y2="1">
          <stop offset="0" stop-color="#e9d3c0"/>
          <stop offset="0.55" stop-color="#6fb6dc"/>
          <stop offset="1" stop-color="#4fa3d2"/>
        </linearGradient>
      </defs>

      <path class="wave-band" fill="var(--blue)"
            d="M0,160 C180,140 360,160 500,200 C590,226 650,245 720,238
               C800,228 860,150 930,135 C1010,120 1100,128 1160,130
               L1160,422 L0,422 Z"/>

      <g class="photo-girl">
        <path d="M580,402 C548,402 540,360 568,348 C560,300 610,282 640,300
                 C660,250 740,245 770,290 C800,275 848,300 832,340
                 C858,355 852,402 815,402 Z"
              fill="url(#girl-tones)" stroke="var(--gold)" stroke-width="11"
              role="img" aria-label="Photo of a smiling girl showing paint-covered hands"/>
      </g>

      <g class="photo-boy">
        <circle cx="968" cy="275" r="118"
                fill="url(#boy-tones)" stroke="var(--gold)" stroke-width="11"
                role="img" aria-label="Photo of a laughing boy holding up paint-covered hands"/>
      </g>
    </svg>

    <div class="brand">
      <span class="brand-dot"></span>
      <span class="brand-name">gtw school</span>
    </div>

    <h1 class="headline">Bilingual <span class="accent">D/E small</span> classes</h1>

    <h2 class="offer-title">DAYCARE</h2>
    <p class="offer-line kindergarten">private kindergarten</p>
    <p class="offer-line school">private school from 2024</p>

    <ul class="contact-list">
      <li>
        <svg class="contact-icon" viewBox="0 0 18 18" aria-hidden="true">
          <circle cx="9" cy="9" r="9" fill="var(--gold)"/>
          <rect x="6" y="4" width="6" height="10" rx="1.2" fill="var(--white)"/>
          <rect x="7" y="5.5" width="4" height="6" fill="var(--gold)"/>
        </svg>
        +41 79 555 01 23
      </li>
      <li>
        <svg class="contact-icon" viewBox="0 0 18 18" aria-hidden="true">
          <circle cx="9" cy="9" r="9" fill="var(--gold)"/>
          <path d="M9,14 C6,10.5 5.3,9 5.3,7.6 A3.7,3.7 0 0 1 12.7,7.6 C12.7,9 12,10.5 9,14 Z" fill="var(--white)"/>
          <circle cx="9" cy="7.6" r="1.4" fill="var(--gold)"/>
        </svg>
        Lindenweg 12, 8000 Musterdorf
      </li>
      <li>
        <svg class="contact-icon" viewBox="0 0 18 18" aria-hidden="true">
          <circle cx="9" cy="9" r="9" fill="var(--gold)"/>
          <g fill="none" stroke="var(--white)" stroke-width="1.2">
            <circle cx="9" cy="9" r="5"/>
            <ellipse cx="9" cy="9" rx="2.2" ry="5"/>
            <line x1="4" y1="9" x2="14" y2="9"/>
          </g>
        </svg>
        www.gtw-daycare.ch
      </li>
    </ul>
  </main>
</body>
</html>
```